Create Business cards for Pet business

Original Business card creation
Please be original. If I wanted a generic business card template, I would have made one myself
Please use colour scheme

Adobe Files like PSD and AI are required
Name : Paul Marsh
Website : [login to view URL]
Phone number :0452817396

```html
<!DOCTYPE html>
<html lang="en">
<head>
<meta charset="utf-8">
<title>Pawshore Business Cards</title>
<link rel="stylesheet" href="https://fonts.googleapis.com/css2?family=Open+Sans:wght@400;600;700&display=swap">
<style>
  :root {
    --canvas: #e9ebee;
    --white: #ffffff;
    --blue: #1a73c4;
    --blue-deep: #0f5ea8;
    --orange: #f39a1c;
    --ink-soft: #3b6fa3;
    --edge: #d4d7dc;
  }
  * { margin: 0; padding: 0; box-sizing: border-box; }
  html, body {
    width: 1200px;
    height: 900px;
    overflow: hidden;
    background: var(--canvas);
    font-family: "Open Sans", sans-serif;
  }
  .stage {
    width: 1200px;
    height: 900px;
    display: flex;
    align-items: center;
    justify-content: center;
    gap: 90px;
  }
  .card {
    position: relative;
    width: 380px;
    height: 580px;
    border-radius: 34px;
    overflow: hidden;
    box-shadow: 0 10px 26px rgba(0, 0, 0, 0.12);
  }
  .card--front { background: var(--white); border: 1px solid var(--edge); }
  .card--back  { background: linear-gradient(160deg, var(--blue) 0%, var(--blue-deep) 100%); }

  .brand {
    display: flex;
    align-items: center;
    gap: 12px;
  }
  .brand__dot {
    width: 26px;
    height: 26px;
    border-radius: 50%;
    background: var(--orange);
  }
  .brand__name {
    font-weight: 700;
    letter-spacing: -0.5px;
  }

  .card--front .brand { position: absolute; top: 44px; left: 40px; }
  .card--front .brand__name { font-size: 44px; color: var(--blue); }

  .holder { position: absolute; top: 118px; left: 42px; }
  .holder__name { font-size: 30px; font-weight: 700; color: var(--blue); line-height: 1.2; }
  .holder__role { font-size: 20px; font-weight: 600; color: var(--orange); margin-top: 2px; }

  .contact { position: absolute; top: 232px; left: 42px; list-style: none; }
  .contact__item {
    display: flex;
    align-items: center;
    gap: 12px;
    font-size: 16px;
    color: var(--orange);
    margin-bottom: 14px;
  }
  .contact__item:nth-child(n+2) { color: var(--ink-soft); }
  .contact__icon {
    width: 26px;
    height: 26px;
    border-radius: 50%;
    background: var(--blue);
    display: flex;
    align-items: center;
    justify-content: center;
    flex: none;
  }
  .contact__icon svg { width: 14px; height: 14px; }

  .front-band {
    position: absolute;
    left: 0;
    bottom: 0;
    width: 100%;
    height: 150px;
  }

  .card--back .brand {
    position: absolute;
    top: 50%;
    left: 50%;
    transform: translate(-50%, -50%);
  }
  .card--back .brand__dot { width: 40px; height: 40px; }
  .card--back .brand__name { font-size: 60px; color: var(--white); }
</style>
</head>
<body>
<main class="stage">
  <section class="card card--front">
    <div class="brand">
      <span class="brand__dot"></span>
      <span class="brand__name">Pawshore</span>
    </div>
    <div class="holder">
      <p class="holder__name">Paul Marsh</p>
      <p class="holder__role">General manager</p>
    </div>
    <ul class="contact">
      <li class="contact__item">
        <span class="contact__icon">
          <svg viewBox="0 0 24 24"><path fill="#fff" d="M6.6 10.8a15.1 15.1 0 0 0 6.6 6.6l2.2-2.2c.3-.3.7-.4 1-.2 1.1.4 2.3.6 3.6.6.6 0 1 .4 1 1V20c0 .6-.4 1-1 1A17 17 0 0 1 3 4c0-.6.4-1 1-1h3.5c.6 0 1 .4 1 1 0 1.3.2 2.5.6 3.6.1.3 0 .7-.2 1l-2.3 2.2z"/></svg>
        </span>
        0452817396
      </li>
      <li class="contact__item">
        <span class="contact__icon">
          <svg viewBox="0 0 24 24"><path fill="#fff" d="M3 5h18v14H3z"/><path fill="none" stroke="#1a73c4" stroke-width="2" d="M3 6l9 7 9-7"/></svg>
        </span>
        paul@pawshore.co
      </li>
      <li class="contact__item">
        <span class="contact__icon">
          <svg viewBox="0 0 24 24"><circle cx="12" cy="12" r="9" fill="none" stroke="#fff" stroke-width="2"/><path fill="none" stroke="#fff" stroke-width="1.6" d="M3 12h18M12 3c3 3 3 15 0 18M12 3c-3 3-3 15 0 18"/></svg>
        </span>
        www.pawshore.co
      </li>
    </ul>
    <svg class="front-band" viewBox="0 0 380 150" preserveAspectRatio="none" aria-hidden="true">
      <path d="M0 70 C 120 20, 250 20, 380 60 L380 150 L0 150 Z" fill="var(--orange)"/>
    </svg>
  </section>

  <section class="card card--back">
    <div class="brand">
      <span class="brand__dot"></span>
      <span class="brand__name">Pawshore</span>
    </div>
  </section>
</main>
</body>
</html>
```